Company brochure for our unique consulting business

We are a small consulting business offering a unique set of services to our clients.. In simple terms we are a business improvement consultancy helping our clients get the best out of their businesses. We work with clients across multiple sectors and deliver a variety of services. We want to put together a brochure to cover these main themes:1. Who we are2. What we do3. The type of people we employ4. The sectors we work inWhile the brochure needs to have a certain corporate feel to it, we don't want it to be "boring" or "stiff". We would like it to have a slightly "friendly" or "informal" feel to it, to reflect the type of organisation we are.We have a company website http://brevalconsultingpartners.net , however we do not want to directly replicate the content or feel as we recognise it needs updating.We would like the brochure to be A4 portrait format. We anticipate requiring 12 sides (including covers) but we are happy to be guided on this based on the content we have provided.The attached ppt file gives the detail of the content to be included and also shows the proposed pagination. For the front cover we would like to try 2 versions, one with the BCP logo and one with the Breval Consulting Partners logo (a file of both is attached)One of the most important pages will be the "Our Services" page. We would like this to cover the centre fold. In the ppt file we have shown an example layout, but this is where we need most help - we are clearly not graphic designers! This page will be the most used page in sales meetings etc.Also attached is the following:1. file for our BrevalConsulting Partners company logo.2. File for our BCP company logo3. Files for Derek's signatures (for under photos) - Owen's to follow4. Photo of Derek & Owen (person in purple shirt to be cropped out)Thank you and really excited to see what everyone comes back with.Derek & Owen

Target Market(s)

Very broad - Manufacturing, Healthcare, Hospitality

Industry/Entity Type

Management Consulting

Font styles to use
Other font styles liked:
• We use Swiss721, but happy to be guided by designer

Colors
3276b5
85abd2
0355a3
333333
5c5c5c
9d9d9d
d9d9d9

Requirements
Must have
• Corporate feel
Nice to have
• Slightly friendly feel
• Our standard "blue" is (CORRECTION) - R55 G96 B146 #376092 and our standard grey is R197 G178, B179 - #B3B2B2, which we would like to keep, but other colours we are happy to be guided on. Brand guidelines attached.

```html
<!DOCTYPE html>
<html lang="en">
<head>
<meta charset="utf-8">
<title>Breval Consulting Partners — Brochure Cover</title>
<link rel="stylesheet" href="https://fonts.googleapis.com/css2?family=Work+Sans:wght@600&display=swap">
<style>
  :root {
    --sky-light: #dbe9f7;
    --sky-mid: #8fb6e0;
    --glass-deep: #3d6fae;
    --paper: #ffffff;
    --navy: #13215c;
    --navy-deep: #0e1a4c;
    --accent-blue: #2a50d2;
    --ink: #111111;
  }
  html, body {
    margin: 0;
    padding: 0;
    overflow: hidden;
    background: var(--paper);
  }
  .cover {
    position: relative;
    width: 848px;
    height: 1200px;
    overflow: hidden;
    background: var(--paper);
  }
  .cover-art {
    position: absolute;
    inset: 0;
    width: 848px;
    height: 1200px;
    display: block;
  }
  .brand-name {
    position: absolute;
    left: 86px;
    top: 392px;
    margin: 0;
    font-family: "Work Sans", "Helvetica Neue", Arial, sans-serif;
    font-weight: 600;
    font-size: 40px;
    line-height: 1.05;
    letter-spacing: -0.5px;
    color: var(--ink);
    transform: rotate(12deg);
    transform-origin: left top;
  }
</style>
</head>
<body>
  <main class="cover">
    <svg class="cover-art" viewBox="0 0 848 1200" xmlns="http://www.w3.org/2000/svg">
      <defs>
        <linearGradient id="skyline-tone" x1="0" y1="0" x2="1" y2="1">
          <stop offset="0" stop-color="var(--glass-deep)"/>
          <stop offset="0.45" stop-color="var(--sky-mid)"/>
          <stop offset="1" stop-color="var(--sky-light)"/>
        </linearGradient>
        <linearGradient id="navy-tone" x1="0" y1="0" x2="0" y2="1">
          <stop offset="0" stop-color="var(--navy)"/>
          <stop offset="1" stop-color="var(--navy-deep)"/>
        </linearGradient>
      </defs>

      <rect class="skyline-photo" x="0" y="0" width="848" height="620" fill="url(#skyline-tone)"
            role="img" aria-label="Photograph looking up at glass office towers against a blue sky"/>

      <polygon class="content-panel" points="0,304 512,478 296,1200 0,1200" fill="var(--paper)"/>
      <polygon class="navy-field" points="512,478 848,592 848,1200 296,1200" fill="url(#navy-tone)"/>
      <polygon class="accent-band" points="542,454 614,475 396,1200 324,1200" fill="var(--accent-blue)"/>
    </svg>

    <h1 class="brand-name">Breval Consulting<br>Partners</h1>
  </main>
</body>
</html>
```